Business card design for new eCommerce site focusing on integrity and strong businsess tactics

We need a business card that will stand out and be memorable. Something with color that matches our company logo colors. Think high end version of Pactivo. There are 2 logos provided. The parent company is called Amber Ledge Partners and we are presenting a new and very exciting eCommerce site called BrightHarborTrade.example.

Target Market(s)

Our target markets are in the Activities, Food and Beverage, Health and Beauty

Industry/Entity Type

Marketing

Contact Information for Business Card

We have 4 members that need cards...I will provide all info to the winner of the design contest
Business Address is
4870 West 63rd Avenue, Suite C207
Phoenix AZ 85731

Font styles to use
Serif
Sans Serif

Colors

Designer to choose colors to be used in the design.

Requirements
Must have
• The card must be memorable...should be unique in design but must exude integrity and be playful .
• I have provided several colors or our parent company...please feel free to use which ever
Nice to have
• I will leave this up to you. Feel free to use other images of your choosing that wraps around our client.....Activities, Dining, Health, Beauty
Should not have
• just dont be boring

```html
<!DOCTYPE html>
<html lang="en">
<head>
<meta charset="utf-8">
<title>BrightHarborTrade.example – Business Card</title>
<link rel="stylesheet" href="https://fonts.googleapis.com/css2?family=Montserrat:wght@300;400;500;600;700&display=swap">
<style>
  :root {
    --canvas: #e4e6e8;
    --card-white: #ffffff;
    --brand-blue: #2f75b3;
    --brand-green: #76bc43;
    --text-gray: #6b6b6b;
    --text-dark: #555555;
    --sym-soft-green: #e8f3df;
    --sym-soft-blue: #e1ecf6;
  }
  * { box-sizing: border-box; margin: 0; padding: 0; }
  html, body {
    width: 1200px; height: 1000px; overflow: hidden;
    background: var(--canvas);
    font-family: "Montserrat", sans-serif;
  }
  .stage { position: relative; width: 1200px; height: 1000px; }

  .card {
    position: absolute; left: 238px; width: 698px; height: 397px;
    border-radius: 14px; overflow: hidden;
    box-shadow: 0 2px 6px rgba(0,0,0,0.18);
  }
  .card--front { top: 82px; background: var(--card-white); }
  .card--back  { top: 520px; background: var(--brand-blue); }

  /* Front */
  .brand { position: absolute; left: 38px; top: 50px; display: flex; align-items: flex-start; gap: 12px; }
  .brand__dot { width: 26px; height: 26px; border-radius: 50%; background: var(--brand-blue); margin-top: 6px; }
  .brand__text { display: flex; flex-direction: column; }
  .brand__name { font-size: 21px; font-weight: 600; color: var(--brand-green); line-height: 1.1; }
  .brand__tagline {
    margin-top: 4px;
    font-size: 11.5px; font-weight: 500; color: var(--text-dark); letter-spacing: 0.7px;
  }

  .brand-symbol-area {
    position: absolute; left: 380px; top: 0; width: 318px; height: 397px;
    background: radial-gradient(ellipse at 55% 45%, var(--sym-soft-blue) 0%, var(--sym-soft-green) 55%, var(--card-white) 80%);
  }

  .person { position: absolute; left: 47px; top: 167px; }
  .person__name { font-size: 19px; font-weight: 600; color: var(--brand-blue); }
  .person__name .first { color: var(--brand-green); }
  .person__role { font-size: 16px; font-weight: 400; color: var(--text-dark); margin-top: 2px; }

  .contacts { position: absolute; left: 49px; top: 232px; list-style: none; }
  .contacts li {
    display: flex; align-items: center; gap: 12px;
    height: 22px; font-size: 14px; font-weight: 400; color: var(--text-gray);
  }
  .contacts svg { width: 12px; height: 12px; fill: none; stroke: var(--brand-blue); stroke-width: 2; }

  .address {
    position: absolute; left: 49px; top: 316px;
    font-size: 15px; font-weight: 400; color: var(--text-gray); line-height: 22px; font-style: normal;
  }

  .band { position: absolute; bottom: 0; height: 20px; }
  .band--green { left: 0; width: 46px; background: var(--brand-green); }
  .band--blue { left: 52px; width: 465px; background: var(--brand-blue); }

  /* Back */
  .back-mark {
    position: absolute; left: 309px; top: 90px; width: 80px; height: 80px;
    border-radius: 50%; border: 5px solid var(--card-white);
  }
  .back-name {
    position: absolute; left: 0; right: 0; top: 256px; text-align: center;
    color: var(--card-white); font-weight: 500; line-height: 1;
  }
  .back-name__main { display: block; font-size: 42px; letter-spacing: 0.2px; }
  .back-name__sub { display: block; font-size: 19px; letter-spacing: 5px; margin-top: 8px; }
  .back-url {
    position: absolute; left: 0; right: 0; top: 353px; text-align: center;
    font-size: 14px; font-weight: 500; color: var(--card-white); letter-spacing: 1.4px;
  }
</style>
</head>
<body>
<main class="stage">

  <section class="card card--front">
    <div class="brand">
      <span class="brand__dot"></span>
      <div class="brand__text">
        <span class="brand__name">BrightHarborTrade.example</span>
        <span class="brand__tagline">Activities-Dining-Health-Beauty</span>
      </div>
    </div>

    <div class="brand-symbol-area" role="img" aria-label="Large brand symbol area"></div>

    <div class="person">
      <p class="person__name"><span class="first">Dorian</span> Welles</p>
      <p class="person__role">Founder</p>
    </div>

    <ul class="contacts">
      <li>
        <svg viewBox="0 0 12 12"><rect x="3" y="1" width="6" height="10" rx="1"/></svg>
        0400 555 017
      </li>
      <li>
        <svg viewBox="0 0 12 12"><rect x="1" y="2.5" width="10" height="7"/><polyline points="1,2.5 6,6.5 11,2.5"/></svg>
        info@brightharbortrade.example
      </li>
      <li>
        <svg viewBox="0 0 12 12"><circle cx="5" cy="5" r="3.3"/><line x1="7.5" y1="7.5" x2="11" y2="11"/></svg>
        www.brightharbortrade.example
      </li>
    </ul>

    <address class="address">
      4870 West 63rd Avenue,<br>
      Suite C207 Phoenix AZ 85731
    </address>

    <div class="band band--green"></div>
    <div class="band band--blue"></div>
  </section>

  <section class="card card--back">
    <span class="back-mark"></span>
    <p class="back-name">
      <span class="back-name__main">Amber Ledge</span>
      <span class="back-name__sub">partners</span>
    </p>
    <p class="back-url">www.amberledgepartners.example</p>
  </section>

</main>
</body>
</html>
```